Combat Sports news website design

Redesigning our existing website to make it more modern, responsive and suitable for our needs. The design needs to take in to account all aspects of our current website structure and services. View the existing website at https://www.ringpulse.co.nz

Particular attention should be paid to our livestream service, which is growing and needs to be much more user friendly to the current experience.

The homepage, article listings and article pages need designs.

Target Market(s)

Combat sports fans

Industry/Entity Type

Media

Coding

Coded - Design and coding required

Number of Pages Required

5+ page

Font styles to use
Sans Serif

Requirements
Must have
• All the functionality of the existing website must be taken in to account, and improved upon.
New design must incorporate our existing logo/colour scheme as this has only just been designed.

```html
<!DOCTYPE html>
<html lang="en">
<head>
<meta charset="utf-8">
<title>Ring Pulse — Kickboxing</title>
<link rel="stylesheet" href="https://fonts.googleapis.com/css2?family=Oswald:wght@500;600;700&family=Roboto:wght@400;500;700&display=swap">
<style>
:root{
  --red:#b0202a;
  --dark:#333333;
  --subnav:#606366;
  --ink:#1c1c1c;
  --muted:#9a9a9a;
  --light:#efefef;
  --line:#dddddd;
  --white:#ffffff;
  --field:#4a4a4a;
}
*{box-sizing:border-box;margin:0;padding:0}
html,body{width:721px;height:1200px;overflow:hidden}
body{position:relative;background:var(--white);font-family:'Roboto',sans-serif;color:var(--ink)}
.abs{position:absolute}
.cond{font-family:'Oswald',sans-serif;font-weight:600;letter-spacing:-.2px}

/* header */
.topbar{left:0;top:0;width:721px;height:36px;background:var(--dark)}
.topbar a{position:absolute;top:10px;color:var(--white);font-size:10px;text-decoration:none}
.topbar .active{font-size:12px;top:8px}
.topbar .underline{position:absolute;left:132px;top:34px;width:81px;height:2px;background:var(--red)}
.brand{position:absolute;left:334px;top:8px;display:flex;align-items:center;gap:4px}
.brand i{display:block;width:8px;height:8px;background:var(--red)}
.brand span{font-family:'Oswald',sans-serif;font-weight:700;font-size:13px;color:var(--white);letter-spacing:.3px}
.subnav{left:0;top:36px;width:721px;height:29px;background:var(--subnav)}
.subnav a{position:absolute;top:8px;font-size:9px;color:#a9acaf;text-decoration:none}
.subnav a.on{color:var(--white)}

/* main */
.section-title{font-size:18px;color:var(--ink)}
.section-title b{color:var(--red);font-weight:600}
.divider{left:442px;top:100px;width:1px;height:634px;background:var(--line)}
.article{left:92px;width:290px;height:134px}
.article .photo{position:absolute;left:0;top:0;width:156px;height:134px}
.article .card{position:absolute;left:158px;top:0;width:130px;height:134px;background:var(--white);box-shadow:1px 1px 3px rgba(0,0,0,.08);padding:9px 8px 0 7px}
.card .cat{font-size:6px;font-weight:500;color:var(--red)}
.card h3{font-family:'Oswald',sans-serif;font-weight:600;font-size:8px;line-height:11.5px;margin-top:3px;height:34px}
.card .date{font-size:4.5px;color:var(--muted);margin-top:4px}
.card p{font-size:5px;line-height:6.5px;color:#333;margin-top:4px;height:32px}
.card .more{position:absolute;left:7px;top:117px;font-size:4.6px;font-weight:500;color:var(--red)}
.btn{background:var(--red);color:var(--white);text-align:center;font-family:'Oswald',sans-serif;font-weight:600}

/* sidebar */
.side-title{font-size:11px;text-align:center;width:168px;left:469px}
.adbox{left:469px;width:168px;background:var(--light);display:flex;align-items:center;justify-content:center;text-align:center;font-family:'Oswald',sans-serif;font-weight:600;font-size:17px;line-height:25px;color:#dedede}
.headline{left:463px;width:185px}
.headline small{display:block;font-size:4.6px;color:#333}
.headline a{display:block;font-size:8.5px;font-weight:500;line-height:10.5px;color:var(--red);text-decoration:none;margin-top:1px}
.poll-q{left:469px;top:647px;font-size:10.5px;color:#222}
.poll{left:469px;width:170px;font-family:'Oswald',sans-serif;font-weight:500;font-size:14px;color:#cfcfcf;white-space:nowrap}
.poll .on{color:var(--red)}

/* footer */
.footer{left:0;top:952px;width:721px;height:248px;background:var(--dark)}
.footer .logo{position:absolute;left:50px;top:14px;display:flex;gap:5px}
.footer .logo i{display:block;width:16px;height:16px;background:var(--red);margin-top:6px}
.footer .logo span{font-family:'Oswald',sans-serif;font-weight:700;font-size:25px;line-height:27px;color:var(--white)}
.bio-name{left:50px;top:89px;font-size:11px;font-weight:700;color:#c8c8c8}
.bio{left:50px;top:104px;width:145px;font-size:8px;line-height:10px;color:#a9a9a9;text-align:justify}
.foot-head{font-size:8px;font-weight:700;color:#555;letter-spacing:.2px}
.foot-links{font-size:8.5px;line-height:12.5px;color:#c8c8c8;letter-spacing:.4px}
.field{left:515px;width:108px;height:13px;background:var(--field);font-size:6px;color:#cfcfcf;padding:3px 6px}
.social{top:188px;width:13px;height:13px;border-radius:50%;background:#8b8b8b}
.copy{left:50px;top:230px;font-size:5px;color:#bdbdbd}
</style>
</head>
<body>

<header class="abs topbar">
  <a class="cond" style="left:82px">HOME</a>
  <a class="cond active" style="left:146px">CATEGORIES</a>
  <span class="underline"></span>
  <a class="cond" style="left:234px">LIVE EVENTS</a>
  <div class="brand"><i></i><span>RING PULSE</span></div>
  <a class="cond" style="left:446px">CONTACT US</a>
  <a class="cond" style="left:512px">ABOUT US</a>
  <a class="cond" style="left:576px">LOGIN &nbsp;/&nbsp; REGISTER</a>
  <svg class="abs" style="left:657px;top:11px" width="13" height="13" viewBox="0 0 13 13" fill="none" stroke="#fff" stroke-width="1.6"><circle cx="5" cy="5" r="3.8"/><line x1="7.8" y1="7.8" x2="12" y2="12"/></svg>
</header>
<nav class="abs subnav">
  <a class="cond" style="left:82px">MMA</a>
  <a class="cond on" style="left:118px">KICKBOXING</a>
  <a class="cond" style="left:176px">BOXING</a>
  <a class="cond" style="left:219px">WRESTLING</a>
  <a class="cond" style="left:275px">XFW</a>
  <a class="cond" style="left:308px">PRIMEFC</a>
</nav>

<h2 class="abs cond section-title" style="left:198px;top:90px"><b>RECENT</b> ARTICLES</h2>
<div class="abs divider"></div>

<article class="abs article" style="top:135px">
  <div class="photo" role="img" aria-label="Two kickboxers exchanging strikes in the ring" style="background:linear-gradient(135deg,#3a2a22 0%,#a0653e 55%,#2a2220 100%)"></div>
  <div class="card"><div class="cat">KICKBOXING</div><h3>Corey Eastwood aims to stay busy in 2021</h3><div class="date">Wednesday 28 Apr, 2021</div><p>Corey Eastwood is a front-running contender in the 80kg division Summit Muay Thai Warrior Series. He will fight Dane Ellison in the quarterfinals, this Saturday, May 1st in Auckland ...</p><div class="more">READ MORE</div></div>
</article>
<article class="abs article" style="top:289px">
  <div class="photo" role="img" aria-label="Event poster showing two fighters for the 80kg bout" style="background:linear-gradient(135deg,#1f2b30,#4a5a55 50%,#2a2420)"></div>
  <div class="card"><div class="cat">KICKBOXING</div><h3>Rawiri Stanton steps into Summit 80kg division on short notice</h3><div class="date">Wednesday 28 Apr, 2021</div><p>Rawiri Stanton is stepping in on short notice to replace the injured Tom Fairlie against Hemi Parker-Gray, in the 80kg division of the Summit Muay Thai Warrior Series this Saturday, May 1.</p><div class="more">READ MORE</div></div>
</article>
<article class="abs article" style="top:443px">
  <div class="photo" role="img" aria-label="Group of cup winners posing with title belts" style="background:linear-gradient(135deg,#6d3a30,#3a3a40 55%,#1e1e22)"></div>
  <div class="card"><div class="cat">KICKBOXING</div><h3>Five WCKA New Zealand Cup winners crowned at Ready to Fight 9</h3><div class="date">Wednesday 28 Apr, 2021</div><p>Paora Hunt, Eti Kauri, Mika Jansen, Henry Yoon and Rob Denton all lifted WCKA NZ Cup titles after winning their fights at Ready to Fight 9 in Auckland.</p><div class="more">READ MORE</div></div>
</article>
<article class="abs article" style="top:597px">
  <div class="photo" role="img" aria-label="Kickboxer landing a kick on his opponent" style="background:linear-gradient(135deg,#2a2622,#b07a55 50%,#3a2a30)"></div>
  <div class="card"><div class="cat">KICKBOXING</div><h3>Charlie Castellanos fights his way to the top</h3><div class="date">Wednesday 28 Apr, 2021</div><p>Corey Eastwood is a front-running contender in the 80kg division Summit Muay Thai Warrior Series. He will fight Dane Ellison in the quarterfinals, this Saturday, May 1st in Auckland ...</p><div class="more">READ MORE</div></div>
</article>
<article class="abs article" style="top:751px">
  <div class="photo" role="img" aria-label="Youth champion in the ring with his title belt under blue lights" style="background:linear-gradient(135deg,#3b30c8,#5a48e0 50%,#221a70)"></div>
  <div class="card"><div class="cat">KICKBOXING</div><h3>Three-time NZ youth champion AJ Fenwick aiming for the top</h3><div class="date">Wednesday 28 Apr, 2021</div><p>Corey Eastwood is a front-running contender in the 80kg division Summit Muay Thai Warrior Series. He will fight Dane Ellison in the quarterfinals, this Saturday, May 1st in Auckland ...</p><div class="more">READ MORE</div></div>
</article>

<div class="abs btn" style="left:208px;top:905px;width:80px;height:22px;font-size:12px;line-height:22px">LOAD MORE</div>

<aside>
  <h4 class="abs cond side-title" style="top:91px">ADVERTISEMENT</h4>
  <div class="abs adbox" style="top:115px;height:119px">YOUR<br>AD<br>HERE</div>
  <h4 class="abs cond side-title" style="top:251px">LATEST HEADLINES</h4>
  <div class="abs headline" style="top:271px"><small>Wednesday 28 Apr, 2021</small><a>Mika Jansen looking to avenge her only loss</a></div>
  <div class="abs headline" style="top:298px"><small>Wednesday 28 Apr, 2021</small><a>Rawiri Stanton steps into Summit 80kg division on short notice</a></div>
  <div class="abs headline" style="top:336px"><small>Wednesday 28 Apr, 2021</small><a>Five WCKA New Zealand Cup winners crowned at Ready to Fight 9</a></div>
  <div class="abs headline" style="top:373px"><small>Wednesday 28 Apr, 2021</small><a>Mika Jansen looking to avenge her only loss</a></div>
  <div class="abs headline" style="top:399px"><small>Wednesday 28 Apr, 2021</small><a>Mika Jansen looking to avenge her only loss</a></div>
  <div class="abs headline" style="top:426px"><small>Wednesday 28 Apr, 2021</small><a>Rawiri Stanton steps into Summit 80kg division on short notice</a></div>
  <h4 class="abs cond side-title" style="top:469px">ADVERTISEMENT</h4>
  <div class="abs adbox" style="top:492px;height:119px">YOUR<br>AD<br>HERE</div>
  <h4 class="abs cond side-title" style="top:628px;left:475px">OPINION AREA</h4>
  <div class="abs poll-q">Select your prefered combat sport</div>
  <div class="abs poll" style="top:663px">MMA &nbsp;&nbsp;<span class="on">Wrestling</span> &nbsp;&nbsp;Kickboxing</div>
  <div class="abs poll" style="top:683px">Boxing &nbsp;&nbsp;&nbsp;Muay Thai &nbsp;&nbsp;XFW &nbsp;&nbsp;&nbsp;ALL</div>
  <div class="abs btn" style="left:469px;top:715px;width:80px;height:23px;font-size:12px;line-height:23px">VOTE</div>
  <div class="abs btn" style="left:556px;top:715px;width:80px;height:23px;font-size:12px;line-height:23px">VIEW RESULTS</div>
</aside>

<footer class="abs footer">
  <div class="logo"><i></i><span>RING<br>PULSE</span></div>
  <div class="abs bio-name">Lena Prescott</div>
  <p class="abs bio">Lena has worked in the media industry since she was 15-years-old. She has worked in both radio and print, and is the co-founder and editor-in-chief of Ring Pulse. As well as being the Ring Pulse Editor, she focuses on writing for muti-discipline combat sports.</p>

  <div class="abs foot-head" style="left:271px;top:24px">SITE MAP</div>
  <div class="abs foot-links" style="left:271px;top:35px">Home<br>MMA<br>Kickboxing<br>Boxing<br>Wrestling<br>XFW<br>PRIMEFC<br>Live events</div>
  <div class="abs foot-head" style="left:367px;top:24px">USEFULL LINKS</div>
  <div class="abs foot-links" style="left:367px;top:35px">Site Terms<br>Advertisement<br>Contact us<br>Privacy</div>

  <div class="abs foot-head" style="left:271px;top:168px">GET IN TOUCH</div>
  <span class="abs social" style="left:268px" role="img" aria-label="Social profile 1"></span>
  <span class="abs social" style="left:299px" role="img" aria-label="Video channel"></span>
  <span class="abs social" style="left:332px" role="img" aria-label="Photo profile"></span>
  <span class="abs social" style="left:365px" role="img" aria-label="Social profile 2"></span>

  <div class="abs foot-head" style="left:271px;top:231px">NEED HELP?</div>
  <svg class="abs" style="left:328px;top:230px" width="14" height="11" viewBox="0 0 14 11"><rect x="0.5" y="0.5" width="13" height="10" fill="#8b8b8b"/><polyline points="1,1 7,6 13,1" fill="none" stroke="#333" stroke-width="1"/></svg>
  <div class="abs" style="left:346px;top:229px;font-size:8.5px;color:#c8c8c8">newsdesk@ringpulse.co.nz</div>

  <div class="abs foot-head" style="left:515px;top:24px">CONTACT US</div>
  <div class="abs field" style="top:37px">First name</div>
  <div class="abs field" style="top:56px">Last name</div>
  <div class="abs field" style="top:74px">Email</div>
  <div class="abs field" style="top:93px">Phone / Mobile</div>
  <div class="abs field" style="top:111px;width:155px;height:92px">Message</div>
  <div class="abs btn" style="left:515px;top:208px;width:47px;height:13px;font-size:9px;line-height:13px">Submit</div>

  <div class="abs copy">Copyright © 2021-2022 RING PULSE All Rights Reserved</div>
</footer>

</body>
</html>
```